Create a flyer for our party getaway to Ibiza.

'The Drifted Ibiza Getaway'

Friday 14th July - Monday 17th July

DJ Varro & DJ Mercer brings together a jam-packed weekend schedule full of the best urban parties in Ibiza.

What's included?

4 Nights Of Entertainment
6 Parties In Total
1 Boat Party
1 Pool Party
2 Superclub Parties
1 Indoor Water Party
Bottomless Drinks (Boat Party Only)
An unbelievable experience
1 unbeatable price.

All this for 140€ (you save 50€ when you book with us)

Tickets avaialble from Tixlane & Gobrino

Target Market(s)

holiday goers

Industry/Entity Type

party, events, club, hip hop

Requirements
Must have
• good vibes
Nice to have
• nice catchy looking title

```html
<!DOCTYPE html>
<html lang="en">
<head>
<meta charset="utf-8">
<title>The Drifted Ibiza Getaway</title>
<link href="https://fonts.googleapis.com/css2?family=Great+Vibes&family=Montserrat:wght@400;500;600;700;800;900&family=Oswald:wght@700&family=Syncopate:wght@700&display=swap" rel="stylesheet">
<style>
  :root{
    --stage:#d9d5dc;
    --night:#0b0620;
    --deep:#1a0a4a;
    --violet:#6a1fc9;
    --purple:#9b30ff;
    --magenta:#d64bff;
    --pink:#e83cff;
    --cyan:#38c6e6;
    --white:#ffffff;
    --navy:#15123a;
    --orange:#f26a1b;
  }
  *{margin:0;padding:0;box-sizing:border-box}
  html,body{width:1200px;height:2400px;overflow:hidden;background:var(--stage)}
  .flyer{
    position:absolute;left:0;top:351px;width:1200px;height:1697px;overflow:hidden;
    background:
      radial-gradient(ellipse 70% 30% at 50% 0%, rgba(155,48,255,.55), transparent 70%),
      linear-gradient(180deg,var(--night) 0%,var(--deep) 18%,#3a1290 45%,#5a1bb8 70%,#2a0c70 88%,var(--night) 100%);
    font-family:"Montserrat",sans-serif;color:var(--white);
  }
  .layer{position:absolute;left:0;top:0;width:1200px;height:1697px}
  .dj-photo{
    position:absolute;left:240px;top:150px;width:700px;height:614px;
    border-radius:260px 260px 0 0;
    background:linear-gradient(180deg,#9a98a6 0%,#d9d8de 45%,#8d8b98 100%);
    box-shadow:0 0 0 6px rgba(56,198,230,.55),0 0 0 12px rgba(155,48,255,.4);
  }
  .blurb{
    position:absolute;left:300px;top:1210px;width:600px;text-align:center;
    font-size:20px;font-weight:600;line-height:1.2;
  }
  .date{position:absolute;top:1262px;font-weight:900;line-height:.95;text-transform:uppercase}
  .date .day{display:block;font-size:86px;letter-spacing:-1px}
  .date .when{display:block;font-size:76px;letter-spacing:-1px}
  .date-start{left:174px}
  .date-start .day{color:var(--white)}
  .date-start .when{color:var(--cyan)}
  .date-end{left:650px}
  .date-end .day{color:var(--cyan)}
  .date-end .when{color:var(--white)}
  .date-link{
    position:absolute;left:544px;top:1300px;width:72px;height:72px;border-radius:50%;
    background:var(--white);color:var(--violet);font-weight:900;font-size:28px;
    display:flex;align-items:center;justify-content:center;
  }
  .perks{
    position:absolute;left:0;top:1426px;width:1200px;height:172px;
    background:linear-gradient(90deg,#7a1fd6,#a733f0 50%,#8a26e0);
  }
  .perk-list{position:absolute;top:30px;list-style:none;font-size:21px;line-height:24px;font-weight:500}
  .perk-list li{position:relative;padding-left:28px}
  .perk-list li::before{
    content:"✓";position:absolute;left:0;top:4px;width:16px;height:16px;border:1.5px solid var(--cyan);
    border-radius:50%;color:var(--cyan);font-size:10px;line-height:14px;text-align:center;
  }
  .perk-list .sub{padding-left:28px}
  .perk-list .sub::before{display:none}
  .perks-a{left:77px}
  .perks-b{left:400px}
  .perks-divider{position:absolute;left:762px;top:18px;height:140px;border-left:2px dashed rgba(255,255,255,.8)}
  .offer{position:absolute;left:814px;top:22px}
  .offer-lead{font-size:31px;font-weight:500}
  .offer-price{font-family:"Syncopate",sans-serif;font-weight:700;font-size:60px;line-height:1;color:var(--pink);letter-spacing:-3px}
  .offer-note{margin-left:9px;margin-top:6px;font-size:19px;font-weight:700;line-height:24px}
  .tickets{
    position:absolute;left:0;top:1598px;width:1200px;height:99px;background:var(--navy);
    display:flex;align-items:center;padding-left:135px;
  }
  .tickets-label{font-size:27px;font-weight:500;letter-spacing:7px;text-transform:uppercase;margin-right:48px}
  .vendor{display:flex;align-items:center;font-size:30px;font-weight:800;margin-right:30px}
  .vendor-mark{width:22px;height:22px;background:var(--orange);margin-right:10px}
</style>
</head>
<body>
<div class="flyer">
  <svg class="layer" viewBox="0 0 1200 1697" aria-hidden="true">
    <defs>
      <linearGradient id="neon" x1="0" x2="1"><stop offset="0" stop-color="#38c6e6"/><stop offset="1" stop-color="#d64bff"/></linearGradient>
    </defs>
    <polygon points="40,42 1160,42 600,660" fill="none" stroke="url(#neon)" stroke-width="5" opacity=".8"/>
    <polygon points="300,180 900,180 600,520" fill="none" stroke="#d64bff" stroke-width="4" opacity=".5"/>
  </svg>

  <div class="dj-photo" role="img" aria-label="Black and white photo of the two DJs posing together in white t-shirts"></div>

  <svg class="layer" viewBox="0 0 1200 1697">
    <defs>
      <linearGradient id="silver" x1="0" y1="0" x2="0" y2="1">
        <stop offset="0" stop-color="#f4f4f7"/><stop offset=".45" stop-color="#b9b9c4"/>
        <stop offset=".55" stop-color="#ffffff"/><stop offset="1" stop-color="#d0d0da"/>
      </linearGradient>
      <linearGradient id="brush" x1="0" x2="1"><stop offset="0" stop-color="#38c6e6"/><stop offset=".5" stop-color="#8a6cf0"/><stop offset="1" stop-color="#d64bff"/></linearGradient>
    </defs>
    <g class="dj-name dj-left" font-family="Oswald, sans-serif" font-weight="700" font-size="178">
      <text transform="translate(275 812) rotate(-90)" textLength="710" lengthAdjust="spacingAndGlyphs" fill="#7a2fbf" opacity=".45">DJ VARRO</text>
      <text transform="translate(233 812) rotate(-90)" textLength="710" lengthAdjust="spacingAndGlyphs" fill="#c24df2">DJ VARRO</text>
    </g>
    <g class="dj-name dj-right" font-family="Oswald, sans-serif" font-weight="700" font-size="178">
      <text transform="translate(1056 812) rotate(-90)" textLength="710" lengthAdjust="spacingAndGlyphs" fill="#2a8fb0" opacity=".45">DJ MERCER</text>
      <text transform="translate(1098 812) rotate(-90)" textLength="710" lengthAdjust="spacingAndGlyphs" fill="#38c6e6">DJ MERCER</text>
    </g>
    <g class="title-banner" transform="rotate(-3 620 780)">
      <polygon points="270,748 960,728 974,812 282,836" fill="url(#brush)"/>
      <text x="620" y="815" text-anchor="middle" font-family="Montserrat, sans-serif" font-weight="900" font-size="80" fill="#fff" textLength="560" lengthAdjust="spacingAndGlyphs">THE DRIFTED</text>
    </g>
    <text class="title-main" x="137" y="1017" font-family="Syncopate, sans-serif" font-weight="700" font-size="240" textLength="957" lengthAdjust="spacingAndGlyphs" fill="url(#silver)" stroke="#8a1fe0" stroke-width="7" paint-order="stroke">IBIZA</text>
    <text class="title-script" x="620" y="1140" text-anchor="middle" font-family="Great Vibes, cursive" font-size="200" fill="#fff">Getaway</text>
  </svg>

  <p class="blurb">DJ Varro &amp; DJ Mercer brings together a jam-packed weekend schedule full of the best urban parties in Ibiza.</p>

  <div class="date date-start"><span class="day">Friday</span><span class="when">14th July</span></div>
  <div class="date-link">TO</div>
  <div class="date date-end"><span class="day">Monday</span><span class="when">17th July</span></div>

  <section class="perks">
    <ul class="perk-list perks-a">
      <li>4 Nights Of Entertainment</li>
      <li>6 Parties In Total</li>
      <li>1 Boat Party</li>
      <li>1 Pool Party</li>
      <li>2 Superclub Parties</li>
    </ul>
    <ul class="perk-list perks-b">
      <li>1 Indoor Water Party</li>
      <li>Bottomless Drinks</li>
      <li class="sub">(Boat Party Only)</li>
      <li>An unbelievable experience</li>
      <li>1 unbeatable price</li>
    </ul>
    <div class="perks-divider"></div>
    <div class="offer">
      <p class="offer-lead">All this for</p>
      <p class="offer-price">140€</p>
      <p class="offer-note">You save 50€ when you<br>book with us</p>
    </div>
  </section>

  <footer class="tickets">
    <span class="tickets-label">Tickets avaialble from</span>
    <span class="vendor"><span class="vendor-mark"></span>Tixlane</span>
    <span class="vendor">Gobrino</span>
  </footer>
</div>
</body>
</html>
```